High-end construction company needs a business card design

We need a modern looking business card that draws people in, is memorable and looks so good people will want to sick it on their fridges.
On the first side what is needed are:
Logo
My name - Tomasz Brelwik
Title - Managing Director
Website - www.varkelt.co.uk
Email - tomasz@varkelt.co.uk
Telephone - 020 5194 6281
Mobile - 07845139072
On the back side was is needed is a list of all the services we provide:
-Kitchen Renovations
-Bathroom Renovations
-House Renovations
-Garage Conversions
-Extensions
-Loft Conversions
-Conservatories
-Carpentry
-Tiling
-Electrical
-Plumbing & Heating
-Bricklaying
-Landscaping
-Decorating
-Plastering
We would like the colours to be the same shades as on the logo with grey or black for the words.
Target Market(s)
Anyone who needs building work done
Contact Information for Business Card
This business card is for a construction company which strives to deliver excellent service and quality.
The look and feel of the card should represent this.
Requirements
Must have
- On the first side what is needed are:
Logo
My name - Tomasz Brelwik
Title - Managing Director
Website - www.varkelt.co.uk
Email - tomasz@varkelt.co.uk
Telephone - 020 5194 6281
Mobile - 07845139072
Nice to have
- Cool looking features

```html
<!DOCTYPE html>
<html lang="en">
<head>
<meta charset="utf-8">
<title>Varkelt Construction – Business Card</title>
<link href="https://fonts.googleapis.com/css2?family=Arimo:wght@400;700&family=Open+Sans:wght@400;600&family=Quicksand:wght@600&display=swap" rel="stylesheet">
<style>
  :root {
    --bg: #eef1ec;
    --card: #ffffff;
    --card-edge: #3a3a3a;
    --charcoal: #353335;
    --band-1: #8c8c8e;
    --band-2: #ababad;
    --band-3: #cfcfd1;
    --green: #7dc242;
    --green-dark: #5e9a2c;
    --ink: #333333;
    --ink-soft: #3c3c3c;
    --ghost: #ececec;
  }
  * { box-sizing: border-box; margin: 0; padding: 0; }
  html, body { width: 1200px; height: 1200px; overflow: hidden; }
  body { background: var(--bg); position: relative; font-family: "Arimo", Arial, sans-serif; }

  .card {
    position: absolute; left: 250px; width: 700px; height: 400px;
    background: var(--card); border: 1.5px solid var(--card-edge);
    border-radius: 22px; overflow: hidden;
  }
  .card--front { top: 190px; }
  .card--back { top: 610px; }

  .front-shape { position: absolute; inset: 0; width: 700px; height: 400px; }

  .brand-name {
    position: absolute; left: 48px; top: 98px; width: 170px; text-align: center;
    font-family: "Arimo", Arial, sans-serif; font-weight: 700; font-size: 36px;
    letter-spacing: 1px; color: #ffffff;
  }

  .person-name {
    position: absolute; left: 475px; top: 62px;
    font-family: "Arimo", Arial, sans-serif; font-weight: 700; font-size: 26px; color: var(--ink);
  }
  .person-title {
    position: absolute; left: 476px; top: 103px;
    font-family: "Quicksand", sans-serif; font-weight: 600; font-size: 16px; color: var(--green);
  }

  .contact-list { position: absolute; left: 280px; top: 218px; list-style: none; }
  .contact-item {
    display: flex; align-items: center; height: 20px; margin-bottom: 18.5px;
    font-family: "Arimo", Arial, sans-serif; font-weight: 700; font-size: 20px; color: var(--green);
  }
  .contact-item:nth-child(3) { margin-bottom: 21px; }
  .contact-icon { width: 22px; height: 22px; margin-right: 25px; flex: none; }

  .brand-ghost {
    position: absolute; left: 0; right: 0; top: 60px; text-align: center;
    font-family: "Arimo", Arial, sans-serif; font-weight: 700; font-size: 120px;
    letter-spacing: 4px; color: var(--ghost);
  }

  .services { position: absolute; left: 0; right: 0; top: 232px; text-align: center; font-family: "Open Sans", sans-serif; }
  .services-title {
    font-weight: 600; font-size: 15px; color: var(--green);
    text-decoration: underline; text-underline-offset: 3px; margin-bottom: 5px;
  }
  .services-line { font-size: 14.5px; line-height: 20.5px; color: var(--ink-soft); }
</style>
</head>
<body>

<section class="card card--front">
  <svg class="front-shape" viewBox="0 0 700 400" aria-hidden="true">
    <path fill="var(--band-3)" d="M0 0 H455 C330 30 245 150 250 280 C252 330 246 370 255 400 H0 Z"/>
    <path fill="var(--band-2)" d="M0 0 H448 C320 35 230 150 236 280 C238 330 232 370 240 400 H0 Z"/>
    <path fill="var(--band-1)" d="M0 0 H440 C310 40 215 150 222 280 C224 330 218 370 226 400 H0 Z"/>
    <path fill="var(--charcoal)" d="M0 0 H430 C300 45 198 150 206 280 C208 330 202 370 210 400 H0 Z"/>
  </svg>

  <div class="brand-name">VARKELT</div>

  <h1 class="person-name">Tomasz Brelwik</h1>
  <p class="person-title">Managing Director</p>

  <ul class="contact-list">
    <li class="contact-item">
      <svg class="contact-icon" viewBox="0 0 22 22" aria-hidden="true">
        <circle cx="11" cy="11" r="10.5" fill="var(--green)"/>
        <path d="M7 5.5c1-.6 1.6 0 2 1l.7 1.7c.2.6 0 1-.5 1.3l-.6.4c.6 1.5 1.6 2.6 3 3.3l.5-.6c.3-.4.8-.6 1.3-.3l1.6.8c.9.4 1.3 1.1.6 2-1 1.3-2.6 1.3-4.6 0-2.4-1.6-4.3-4.1-4.7-6.3-.2-1.4.1-2.6.7-3.3z" fill="var(--charcoal)"/>
      </svg>07845139072
    </li>
    <li class="contact-item">
      <svg class="contact-icon" viewBox="0 0 22 22" aria-hidden="true">
        <circle cx="11" cy="11" r="10.5" fill="var(--green)"/>
        <path d="M5 9c0-2 12-2 12 0v1.2h-3V9H8v1.2H5z M7 11h8l1.5 4.5h-11z" fill="var(--charcoal)"/>
        <circle cx="11" cy="13" r="1.2" fill="var(--green)"/>
      </svg>020 5194 6281
    </li>
    <li class="contact-item">
      <svg class="contact-icon" viewBox="0 0 22 22" aria-hidden="true">
        <circle cx="11" cy="11" r="10.5" fill="var(--green)"/>
        <rect x="5.5" y="7" width="11" height="8" fill="var(--charcoal)"/>
        <path d="M5.5 7l5.5 4.5L16.5 7" fill="none" stroke="var(--green)" stroke-width="1"/>
      </svg>tomasz@varkelt.co.uk
    </li>
    <li class="contact-item">
      <svg class="contact-icon" viewBox="0 0 22 22" aria-hidden="true">
        <circle cx="11" cy="11" r="10.5" fill="var(--green)"/>
        <g fill="none" stroke="var(--charcoal)" stroke-width="1">
          <circle cx="11" cy="11" r="6"/>
          <ellipse cx="11" cy="11" rx="2.6" ry="6"/>
          <path d="M5 11h12M6 8h10M6 14h10"/>
        </g>
      </svg>www.varkelt.co.uk
    </li>
  </ul>
</section>

<section class="card card--back">
  <div class="brand-ghost" aria-hidden="true">VARKELT</div>
  <div class="services">
    <h2 class="services-title">Services</h2>
    <p class="services-line">• Kitchen Renovations • Bathroom Renovations • House Renovations</p>
    <p class="services-line">• Garage Conversions &nbsp;• Extensions • Loft Conversions</p>
    <p class="services-line">• Conservatories • Carpentry • Tiling • Electrical • Plumbing &amp; Heating</p>
    <p class="services-line">• Bricklaying • Landscaping • Decorating • Plastering</p>
  </div>
</section>

</body>
</html>
```